Harbor Lanterns Remember

The song is an instrumental song that was built around a slide show with an original poem, "Carry the Ember". I would like to do an Melvo digital booklet if possible.

The general vision for the album cover/possible Melvo digital booklet is a person coming from a dark place and just seeing a glimpse of light (representing hope of a better day).

Stills from the movie attached for reference.

Watch the movie on Vidra .... http://vidra.cx/Kq4pWmTz2Ha

```html
<!DOCTYPE html>
<html lang="en">
<head>
<meta charset="utf-8">
<title>Harbor Lanterns Remember – Dale Varrick</title>
<link rel="stylesheet" href="https://fonts.googleapis.com/css2?family=Caveat+Brush&family=Oswald:wght@600&display=swap">
<style>
  :root {
    --ink-black: #000000;
    --glow-white: #fffaf0;
    --glow-amber: #ff9a4a;
    --glow-ember: #a8380f;
    --title-light: #ffe3d2;
    --title-orange: #e8612a;
    --artist-orange: #c9512f;
  }
  html, body {
    margin: 0;
    padding: 0;
    overflow: hidden;
    background: var(--ink-black);
  }
  .cover {
    position: relative;
    width: 1200px;
    height: 1200px;
    overflow: hidden;
    background: var(--ink-black);
  }
  .cover-photo {
    position: absolute;
    inset: 0;
    width: 1200px;
    height: 1200px;
  }
  .album-title {
    position: absolute;
    top: 92px;
    left: 0;
    width: 1200px;
    margin: 0;
    text-align: center;
    font-family: "Caveat Brush", cursive;
    font-weight: 400;
    font-size: 112px;
    line-height: 1;
    letter-spacing: -1px;
    white-space: nowrap;
    background: linear-gradient(180deg, var(--title-light) 20%, var(--title-orange) 75%);
    -webkit-background-clip: text;
    background-clip: text;
    color: transparent;
  }
  .artist-name {
    position: absolute;
    right: 26px;
    bottom: 44px;
    margin: 0;
    font-family: "Oswald", sans-serif;
    font-weight: 600;
    font-size: 68px;
    line-height: 1;
    letter-spacing: -1px;
    color: var(--artist-orange);
    transform: scaleX(0.88);
    transform-origin: right bottom;
  }
</style>
</head>
<body>
  <main class="cover">
    <svg class="cover-photo" viewBox="0 0 1200 1200" role="img" aria-label="Photo of a dark brick tunnel with a bright arched opening of light at its far end">
      <defs>
        <radialGradient id="tunnel-light" cx="596" cy="470" r="560" gradientUnits="userSpaceOnUse" gradientTransform="translate(596 470) scale(0.75 1) translate(-596 -470)">
          <stop offset="0" stop-color="var(--glow-white)"/>
          <stop offset="0.14" stop-color="var(--glow-white)"/>
          <stop offset="0.22" stop-color="var(--glow-amber)"/>
          <stop offset="0.38" stop-color="var(--glow-ember)" stop-opacity="0.6"/>
          <stop offset="0.62" stop-color="#2a0b03" stop-opacity="0.5"/>
          <stop offset="1" stop-color="var(--ink-black)"/>
        </radialGradient>
      </defs>
      <rect width="1200" height="1200" fill="var(--ink-black)"/>
      <rect width="1200" height="1200" fill="url(#tunnel-light)"/>
    </svg>
    <h1 class="album-title">Harbor Lanterns Remember</h1>
    <p class="artist-name">DALE VARRICK</p>
  </main>
</body>
</html>
```